Home Security Company Business Card

Looking for a eye catching business card that is non traditional and stands out but yet still looks professional. It should include all the pertinent information such as name, title, address, telephone, e-mail, website address should definitely stand out and then finally the logo.

Target Market(s)

Residential and Commercial accounts mostly upscale accounts

Industry/Entity Type

Security

Contact Information for Business Card

Name
Title
Address
Office #
Cell #
E-mail
Website

Font styles to use
Serif
Sans Serif

Requirements
Must have
• Logo, two sided color configuration
Nice to have
• You decide
Should not have
• There really aren't any.

```html
<!DOCTYPE html>
<html lang="en">
<head>
<meta charset="utf-8">
<title>Bastion Security Systems – Business Card</title>
<link href="https://fonts.googleapis.com/css2?family=Source+Sans+3:wght@400;600&display=swap" rel="stylesheet">
<style>
  :root {
    --stage: #3b3b3b;
    --crimson: #741006;
    --crimson-deep: #5e0c04;
    --gold: #e4a83e;
    --gold-light: #f0c46a;
    --gold-dark: #c07e2a;
    --paper: #fafafa;
    --ink-light: #ffffff;
  }
  * { box-sizing: border-box; margin: 0; padding: 0; }
  html, body { width: 1200px; height: 750px; overflow: hidden; }
  body {
    background: var(--stage);
    font-family: "Source Sans 3", "Myriad Pro", sans-serif;
    position: relative;
  }
  .card {
    position: absolute;
    top: 228px;
    width: 461px;
    height: 263px;
    overflow: hidden;
  }
  .card--front {
    left: 124px;
    background: var(--crimson);
  }
  .card--back {
    left: 618px;
    background: var(--paper);
  }
  .front__panel {
    position: absolute;
    top: 0; right: 0;
    width: 26%;
    height: 100%;
    background: radial-gradient(ellipse at 40% 45%, var(--gold-light), var(--gold) 55%, var(--gold-dark));
  }
  .contact {
    position: absolute;
    left: 32px;
    top: 26px;
    color: var(--ink-light);
  }
  .contact__name {
    color: var(--gold);
    font-weight: 600;
    font-size: 17px;
    line-height: 20px;
  }
  .contact__title {
    font-size: 12.5px;
    line-height: 15px;
  }
  .contact__address {
    margin-top: 12px;
    font-size: 11px;
    line-height: 14px;
  }
  .contact__lines {
    list-style: none;
    margin-top: 8px;
    font-size: 11px;
    line-height: 17.5px;
  }
  .contact__lines li {
    display: flex;
    align-items: center;
    gap: 6px;
  }
  .contact__lines svg { width: 11px; height: 11px; flex: none; }
  .brand-name {
    position: absolute;
    left: 32px;
    top: 186px;
    color: var(--ink-light);
    font-weight: 600;
    text-transform: uppercase;
  }
  .brand-name__main { display: block; font-size: 30px; line-height: 30px; letter-spacing: 0.5px; }
  .brand-name__sub { display: block; font-size: 30px; line-height: 30px; letter-spacing: 0.5px; }
  .brand-name__sub { font-size: 14px; line-height: 16px; }
  .back__mark {
    position: absolute;
    left: 130px;
    top: 104px;
    display: flex;
    align-items: center;
    gap: 10px;
    color: var(--crimson);
    font-weight: 600;
    text-transform: uppercase;
  }
  .back__dot {
    width: 40px; height: 40px;
    border-radius: 50%;
    background: var(--crimson);
  }
  .back__mark .brand-name__main { font-size: 20px; line-height: 20px; }
  .back__mark .brand-name__sub { font-size: 9.5px; line-height: 12px; }
  .back__band {
    position: absolute;
    left: 0; bottom: 0;
    width: 100%;
    height: 8px;
    background: var(--crimson);
  }
</style>
</head>
<body>
  <section class="card card--front" aria-label="Business card front">
    <div class="front__panel"></div>
    <div class="contact">
      <p class="contact__name">Daniel Harper</p>
      <p class="contact__title">CEO/Founder</p>
      <p class="contact__address">4120 Juniper Court<br>Fairbanks, Alaska 99701</p>
      <ul class="contact__lines">
        <li>
          <svg viewBox="0 0 12 12" aria-hidden="true"><path fill="var(--gold)" d="M2.5 0.8 4.3 3.2 3.3 4.5c.7 1.6 2 2.9 3.6 3.6l1.3-1 2.4 1.8-.9 2.1C5 10.8 1 6.8.4 1.7z"/></svg>
          <span>555 214 7730</span>
        </li>
        <li>
          <svg viewBox="0 0 12 12" aria-hidden="true"><rect x="3" y="0.5" width="6" height="11" rx="1" fill="var(--gold)"/><rect x="4" y="2" width="4" height="7" fill="var(--crimson)"/></svg>
          <span>555 381 0496</span>
        </li>
        <li>
          <svg viewBox="0 0 12 12" aria-hidden="true"><rect x="0.5" y="2.5" width="11" height="7" fill="var(--gold)"/><path d="M0.5 2.5 6 6.5 11.5 2.5" fill="none" stroke="var(--crimson)" stroke-width="1"/></svg>
          <span>daniel@bastionsec.com</span>
        </li>
        <li>
          <svg viewBox="0 0 12 12" aria-hidden="true"><circle cx="6" cy="6" r="5.5" fill="var(--gold)"/><path d="M6 0.5v11M0.5 6h11M3 2c2 2 2 6 0 8M9 2c-2 2-2 6 0 8" fill="none" stroke="var(--crimson)" stroke-width="0.8"/></svg>
          <span>www.bastionsec.com</span>
        </li>
      </ul>
    </div>
    <p class="brand-name">
      <span class="brand-name__main">Bastion</span>
      <span class="brand-name__sub">Security Systems Inc.</span>
    </p>
  </section>

  <section class="card card--back" aria-label="Business card back">
    <div class="back__mark">
      <span class="back__dot"></span>
      <p>
        <span class="brand-name__main">Bastion</span>
        <span class="brand-name__sub">Security Systems Inc.</span>
      </p>
    </div>
    <div class="back__band"></div>
  </section>
</body>
</html>
```